Harborline Renewal Business Card Design

Professional and clean design. The design colors should flow with the logo. Two-sided card with the website on the back which is:

www.HarborlineRenewal.example.

"Specializing in Water Damage Restoration"

On the front I need the name, email, phone, and logo.

Name: Darnell Quisby
Email: Darnell@HarborlineRenewal.example
Phone: 555-318-2046 for now

I only have the Preview and Thumbnail right now but should have the source files uploaded within a day or two.

Target Market(s)

Flood victims, home owners with water damage from busted pipes etc...

Industry/Entity Type

Business

Contact Information for Business Card

Name: Darnell Quisby

Font styles to use
Serif
Sans Serif

Requirements
Must have
• Business Card Details Info

```html
<!DOCTYPE html>
<html lang="en">
<head>
<meta charset="utf-8">
<title>Harborline Renewal Business Card</title>
<link rel="stylesheet" href="https://fonts.googleapis.com/css2?family=Open+Sans:wght@400;600;700&display=swap">
<style>
  :root {
    --blue: #2a93d5;
    --blue-light: #4fbdee;
    --blue-faint: #e6f3fb;
    --paper: #ffffff;
    --backdrop: #e9ecef;
    --ink-shadow: rgba(20, 40, 60, 0.18);
  }
  * { box-sizing: border-box; margin: 0; padding: 0; }
  html, body {
    width: 1200px; height: 900px; overflow: hidden;
    background: var(--backdrop);
    font-family: "Open Sans", Arial, sans-serif;
  }
  .canvas { position: relative; width: 1200px; height: 900px; }
  .card {
    position: absolute; left: 270px; width: 660px; height: 377px;
    background: var(--paper); border-radius: 22px; overflow: hidden;
    box-shadow: 0 10px 30px var(--ink-shadow);
  }
  .card--back { top: 48px; }
  .card--front { top: 475px; }
  .band { position: absolute; left: 0; bottom: 0; width: 660px; height: 90px; }

  /* back side */
  .back-brand {
    position: absolute; left: 150px; top: 40px; width: 210px; height: 210px;
    border: 9px solid var(--blue); border-radius: 50%;
    display: flex; align-items: center; justify-content: center; text-align: center;
  }
  .back-brand__name {
    font-weight: 700; font-size: 25px; line-height: 1.15; color: var(--blue);
    letter-spacing: 1px; text-transform: uppercase;
  }
  .back-info {
    position: absolute; right: 34px; top: 266px; text-align: right; color: var(--blue);
  }
  .back-info__tagline { font-size: 14px; letter-spacing: 0.6px; text-transform: uppercase; line-height: 20px; }
  .back-info__web { font-size: 15px; font-weight: 600; line-height: 20px; margin-top: 2px; }

  /* front side */
  .front-deco {
    position: absolute; left: 330px; top: -70px; width: 380px; height: 380px;
    border-radius: 50%; background: var(--blue-faint);
  }
  .front-brand {
    position: absolute; left: 38px; top: 60px; display: flex; align-items: center; gap: 12px;
  }
  .front-brand__dot { width: 44px; height: 44px; border-radius: 50%; background: var(--blue-light); flex: none; }
  .front-brand__name {
    font-weight: 700; font-size: 27px; color: var(--blue); letter-spacing: 1.5px; text-transform: uppercase;
  }
  .front-name {
    position: absolute; right: 30px; top: 148px; display: flex; align-items: flex-end; width: 600px;
  }
  .front-name__rule { flex: 1; height: 2px; background: var(--blue); margin-right: 10px; margin-bottom: 4px; }
  .front-name__text {
    font-weight: 700; font-size: 24px; color: var(--blue); letter-spacing: 1px; text-transform: uppercase;
  }
  .contact-list {
    position: absolute; left: 38px; top: 230px; list-style: none; color: var(--blue);
  }
  .contact-list__item { display: flex; align-items: center; gap: 10px; font-size: 15px; line-height: 24px; }
  .contact-list__icon { width: 14px; height: 14px; flex: none; }
</style>
</head>
<body>
<main class="canvas">

  <section class="card card--back" aria-label="Card back">
    <div class="back-brand">
      <span class="back-brand__name">Harborline<br>Renewal</span>
    </div>
    <div class="back-info">
      <p class="back-info__tagline">Specializing in Water Damage Restoration</p>
      <p class="back-info__web">www.HarborlineRenewal.example</p>
    </div>
    <svg class="band" viewBox="0 0 660 90" preserveAspectRatio="none" aria-hidden="true">
      <polygon points="0,58 660,40 660,90 0,90" fill="var(--blue-light)"/>
      <polygon points="0,68 250,62 275,48 660,40 660,90 0,90" fill="var(--blue)"/>
      <polygon points="300,60 660,52 660,90 300,90" fill="var(--blue-light)"/>
    </svg>
  </section>

  <section class="card card--front" aria-label="Card front">
    <div class="front-deco"></div>
    <div class="front-brand">
      <span class="front-brand__dot"></span>
      <span class="front-brand__name">Harborline Renewal</span>
    </div>
    <div class="front-name">
      <span class="front-name__rule"></span>
      <span class="front-name__text">Darnell Quisby</span>
    </div>
    <ul class="contact-list">
      <li class="contact-list__item">
        <svg class="contact-list__icon" viewBox="0 0 16 16" aria-hidden="true"><path d="M4 1 L6.5 4.5 L5 6.5 C6 8.5 7.5 10 9.5 11 L11.5 9.5 L15 12 L13 15 C7 14.5 1.5 9 1 3 Z" fill="var(--blue)"/></svg>
        <span>555-318-2046</span>
      </li>
      <li class="contact-list__item">
        <svg class="contact-list__icon" viewBox="0 0 16 16" aria-hidden="true"><rect x="1" y="3" width="14" height="10" fill="none" stroke="var(--blue)" stroke-width="1.6"/><path d="M1 3 L8 9 L15 3" fill="none" stroke="var(--blue)" stroke-width="1.6"/></svg>
        <span>Darnell@HarborlineRenewal.example</span>
      </li>
      <li class="contact-list__item">
        <svg class="contact-list__icon" viewBox="0 0 16 16" aria-hidden="true"><circle cx="8" cy="8" r="6.5" fill="none" stroke="var(--blue)" stroke-width="1.5"/><path d="M1.5 8 H14.5 M8 1.5 C5 5 5 11 8 14.5 M8 1.5 C11 5 11 11 8 14.5" fill="none" stroke="var(--blue)" stroke-width="1.2"/></svg>
        <span>www.HarborlineRenewal.example</span>
      </li>
    </ul>
    <svg class="band" viewBox="0 0 660 90" preserveAspectRatio="none" aria-hidden="true">
      <polygon points="0,80 660,62 660,90 0,90" fill="var(--blue-light)"/>
      <polygon points="0,84 660,70 660,90 0,90" fill="var(--blue)"/>
      <polygon points="520,20 660,16 660,90 520,90" fill="var(--blue)"/>
    </svg>
  </section>

</main>
</body>
</html>
```